wardrobe/costume stylist needs good business card for own business

Hi:)

I'm wanting a business card for my company. I am a freelance stylist.

I do wardrobe/costume stylist to TV commercials; Films; Fashion and Lifestyle shoots.

I'd like a design based around my name Rosalind Parfrey written nicely, maybe a colour? Up to you?!

I've attached a couple of images of business cards I like
.... be creative and have fun!

Thank you :)

Reason: I was trying to get my new business card ready for before I headed overseas Friday morning but I don't think that was realistic so I'd like to extend the deadline to give time to the project. Thank you

Hi designers:) Thank you for all your designs, I've extended the deadline until Sunday, so there's a bit more time. I've attached 3 pictures of business cards which I quite like, please take a look to see if it can be of help in your process. I like the pale plain or patterned background with dark font and the dark plain or patterned background with the pale font the motifs the feminine fonts the plain fonts I like the idea of playing with a circle or some shape on one side of the card with my name or initials as in the picture I have on my post could you play around with this idea a bit please? Thank you all for the work you've done :) Rosa

Hi I am working overseas til Saturday night sorry for no feedback until I teturn Thanks :) Rosa

Hi designers, Thank you all so much for submitting your designs, I really appreciate your input into my project :) I'm sorry I didn't get to respond to some comments, and give feedback. I didn't back from being away until later than I expected, and the deadline had passed then, so apologies. Thanks to you all again for all your really good designs :) Rosa

Target Market(s)

I am a freelance stylist my target audience is producers, production companies, photographers, directors...

Industry/Entity Type

Business

Requirements
Must have
• Rosalind Parfrey
Stylist or Wardrobe Stylist

email rosaparfrey@mailbox-example.co.nz
Mobile 0218467193

(Don't have to use the words 'email' and 'mobile')
Nice to have
• Would like it to be double sided
Like B & W
Like pale colour background with dark font or white font
Like dark colour background with pale font
Should not have
• I would prefer it not to incorporate pictures

```html
<!DOCTYPE html>
<html lang="en">
<head>
<meta charset="utf-8">
<title>Rosalind Parfrey – Business Card</title>
<link href="https://fonts.googleapis.com/css2?family=Cormorant+Garamond:wght@500&family=Open+Sans:wght@400&display=swap" rel="stylesheet">
<style>
  :root {
    --stage: #2e2e2e;
    --card-light: #ffffff;
    --card-dark: #000000;
    --gold: #c9a24f;
    --gold-ring: #b8923a;
    --ink: #1a1a1a;
    --pale: #d6d6d6;
  }
  * { margin: 0; padding: 0; box-sizing: border-box; }
  html, body {
    width: 1200px;
    height: 655px;
    overflow: hidden;
    background: var(--stage);
  }
  .canvas {
    position: relative;
    width: 1200px;
    height: 655px;
  }
  .card {
    position: absolute;
    top: 213px;
    width: 393px;
    height: 228px;
  }
  .card--front {
    left: 207px;
    background: var(--card-light);
  }
  .card--back {
    left: 600px;
    background: var(--card-dark);
  }
  .front-mark {
    position: absolute;
    left: 50%;
    top: 40px;
    width: 116px;
    height: 116px;
    margin-left: -58px;
    border-radius: 50%;
    background: var(--gold);
  }
  .front-name {
    position: absolute;
    left: 0;
    right: 0;
    top: 170px;
    text-align: center;
    font-family: "Cormorant Garamond", serif;
    font-weight: 500;
    font-size: 22px;
    letter-spacing: 2px;
    color: var(--ink);
  }
  .back-ring {
    position: absolute;
    left: 130px;
    top: 55px;
    width: 118px;
    height: 118px;
    border-radius: 50%;
    border: 1.5px solid var(--gold-ring);
  }
  .back-name {
    position: absolute;
    left: 0;
    right: 0;
    top: 92px;
    text-align: center;
    font-family: "Cormorant Garamond", serif;
    font-weight: 500;
    font-size: 34px;
    letter-spacing: 2px;
    color: var(--pale);
    line-height: 40px;
  }
  .role {
    position: absolute;
    left: 50px;
    right: 50px;
    top: 184px;
    display: flex;
    align-items: center;
    gap: 8px;
    font-family: "Cormorant Garamond", serif;
    font-weight: 500;
    font-size: 11.5px;
    letter-spacing: 0.6px;
    text-transform: uppercase;
    color: var(--gold);
    white-space: nowrap;
  }
  .role::before, .role::after {
    content: "";
    flex: 1;
    height: 1px;
    background: var(--gold);
  }
  .contact {
    position: absolute;
    left: 0;
    right: 0;
    top: 198px;
    text-align: center;
    font-family: "Open Sans", sans-serif;
    font-size: 9.5px;
    color: var(--gold);
  }
</style>
</head>
<body>
  <main class="canvas">
    <section class="card card--front" aria-label="Card front">
      <div class="front-mark"></div>
      <p class="front-name">Rosalind Parfrey</p>
    </section>
    <section class="card card--back" aria-label="Card back">
      <div class="back-ring"></div>
      <h1 class="back-name">rosalind parfrey</h1>
      <p class="role">Stylist or Wardrobe Stylist</p>
      <p class="contact">rosaparfrey@mailbox-example.co.nz | 0218467193</p>
    </section>
  </main>
</body>
</html>
```